Marta's Dwellings website

We need a simple website for our property investment business in the UK. We basically need our contact details and brief description.We have the company logo already done (via ArtFlockly) so please use these:https://drive.google.com/drive/folders/1szJ3iRhelElZ40NIFT7w-c14MaY3Y_oV?usp=sharingYou could use some stock photos of UK houses for now.Let me know when to provide more detailed descriptions, etc

Coding

Coded - Design and coding required

Number of Pages Required

1 page

Colors

Designer to choose colors to be used in the design.

```html
<!DOCTYPE html>
<html lang="en">
<head>
<meta charset="utf-8">
<title>Marta's Dwellings</title>
<link href="https://fonts.googleapis.com/css2?family=Nunito+Sans:wght@300;400;600;700;800&display=swap" rel="stylesheet">
<style>
:root{
  --ink:#1d1d1f;
  --dark:#232325;
  --darker:#161617;
  --white:#ffffff;
  --muted:#3a3a3a;
  --line:#e4e4e4;
  --star:#f5d20a;
  --sky:#7f9bb8;
  --brick:#8a5a44;
  --leaf:#4e6b3a;
}
*{margin:0;padding:0;box-sizing:border-box}
html,body{width:1200px;height:5168px;overflow:hidden}
body{position:relative;background:var(--white);font-family:"Nunito Sans",sans-serif;color:var(--ink)}
.abs{position:absolute}
.wordmark{font-weight:400;letter-spacing:.55em;text-transform:uppercase;white-space:nowrap}

/* header */
.site-header{top:0;left:0;width:1200px;height:140px}
.brand{left:88px;top:22px;width:260px;text-align:center}
.brand-square{display:block;width:34px;height:34px;background:var(--ink);margin:0 auto 28px}
.brand .wordmark{font-size:15px;color:var(--ink)}
.support{left:660px;top:22px;display:flex;gap:12px;align-items:center}
.support-icon{width:40px;height:40px}
.support strong{display:block;font-size:15px;font-weight:800}
.support span{font-size:16px}
.login{left:886px;top:18px;width:222px;height:54px;border-radius:27px;background:var(--dark);color:var(--white);font-weight:800;font-size:16px;display:flex;align-items:center;justify-content:center;gap:8px}
.main-nav{top:102px;left:506px;display:flex;gap:44px;font-size:15px;text-transform:uppercase}

/* hero */
.hero{top:140px;left:0;width:1200px;height:650px;clip-path:polygon(0 0,1200px 0,1200px 564px,600px 610px,0 650px)}
.hero-photo{width:100%;height:100%;background:linear-gradient(180deg,#9fb4c8 0%,#7d8f8e 35%,#6b5545 60%,#3f5230 82%,#2c3a22 100%)}
.hero-mark{top:288px;left:0;width:1200px;text-align:center}
.hero-square{display:block;width:96px;height:96px;background:var(--white);margin:0 auto 60px}
.hero-mark .wordmark{font-size:46px;color:var(--white)}

/* about */
.about-hex{left:74px;top:940px;width:486px;height:422px}
.about-copy{left:596px;top:972px;width:512px}
h2{font-size:34px;font-weight:800;text-transform:uppercase;letter-spacing:.01em}
.about-copy p{margin-top:18px;font-size:16px;line-height:36px;text-align:justify;color:var(--muted)}
.btn{display:flex;align-items:center;justify-content:center;gap:6px;border-radius:28px;background:var(--dark);color:var(--white);font-weight:800;font-size:16px;text-transform:uppercase}
.read-more{left:596px;top:1264px;width:210px;height:56px}

/* features */
.features{top:1510px;left:0;width:1200px;height:760px}
.feature-list{left:686px;top:1608px;width:430px;color:var(--white)}
.feature-list h2{color:var(--white)}
.feature{margin-top:42px}
.feature:first-of-type{margin-top:28px}
.feature h3{font-size:21px;font-weight:800;text-transform:uppercase}
.feature p{margin-top:10px;font-size:14px;line-height:31px;color:#d9d9d9}
.feature-icon{left:574px;width:80px;height:80px;border-radius:50%;background:var(--white);border:3px solid var(--darker);display:flex;align-items:center;justify-content:center}

/* projects */
.projects-head{top:2360px;left:0;width:1200px;text-align:center}
.projects-head p{margin:18px auto 0;width:880px;font-size:16px;line-height:31px;color:var(--muted)}
.project{width:332px;height:214px}
.project-caption{position:absolute;top:96px;left:0;width:100%;text-align:center;color:var(--white);font-size:17px;font-weight:300}
.slide-arrow{width:44px;height:30px}

/* testimonials */
.testimonials{top:3110px;left:0;width:1200px;height:720px}
.testimonial{top:3362px;left:130px;width:940px;text-align:center;color:var(--white)}
.testimonial h2{color:var(--white)}
.stars{margin-top:16px;display:flex;gap:6px;justify-content:center}
.testimonial p{margin-top:12px;font-size:16px;line-height:36px;text-align:justify;text-align-last:center;color:#e8e8e8}
.testimonial .name{margin-top:10px;font-size:24px;font-weight:800;text-transform:uppercase}

/* contact */
.contact-head{top:3966px;left:0;width:1200px;text-align:center}
.contact-item{width:300px;text-align:center;font-size:16px;line-height:28px}
.contact-icon{display:block;width:84px;height:84px;border-radius:50%;background:var(--dark);margin:0 auto 18px}
.contact-item strong{font-weight:800}
.field{height:48px;border:3px solid #f0f0f0;border-bottom-width:4px;font-size:12px;color:#555;padding:12px 14px;display:flex;gap:6px;align-items:flex-start}
.field.message{height:152px}
.submit{left:496px;top:4454px;width:208px;height:56px}

/* footer */
.site-footer{top:4640px;left:0;width:1200px;height:528px}
.footer-inner{top:4820px;left:0;width:1200px;text-align:center;color:var(--white)}
.footer-square{display:block;width:96px;height:96px;background:var(--white);margin:0 auto 48px}
.footer-inner .wordmark{font-size:30px}
.footer-nav{margin-top:24px;font-size:15px;font-weight:800;text-transform:uppercase;display:flex;justify-content:center;gap:14px}
.copyright{margin-top:16px;font-size:15px;color:#dcdcdc}
.socials{margin-top:14px;display:flex;justify-content:center;gap:8px}
.socials span{width:30px;height:30px;border-radius:50%;border:2px solid var(--white)}
</style>
</head>
<body>

<header class="site-header abs">
  <div class="brand abs"><span class="brand-square"></span><span class="wordmark">Marta's Dwellings</span></div>
  <div class="support abs">
    <svg class="support-icon" viewBox="0 0 40 40"><circle cx="20" cy="20" r="18" fill="none" stroke="#1d1d1f" stroke-width="3"/><path d="M13 11c2-1 3 0 4 2l1 3c0 1-1 2-2 3 1 3 3 5 6 6 1-1 2-2 3-2l3 1c2 1 3 2 2 4-1 2-3 3-5 2-6-2-11-7-13-13-1-2 0-4 1-6z" fill="#1d1d1f"/></svg>
    <div><strong>SUPPORT CALL US</strong><span>888 888 8888</span></div>
  </div>
  <div class="login abs"><svg width="14" height="16" viewBox="0 0 14 16"><circle cx="7" cy="4" r="4" fill="#fff"/><path d="M0 16c0-5 3-7 7-7s7 2 7 7z" fill="#fff"/></svg>LOGIN / SIGN UP</div>
  <nav class="main-nav abs"><span>Home</span><span>About Us</span><span>Our Projects</span><span>Testimonials</span><span>Contact</span></nav>
</header>

<section class="hero abs">
  <div class="hero-photo" role="img" aria-label="Photo of a canal lined with brick warehouses and modern flats under a cloudy sky"></div>
</section>
<div class="hero-mark abs"><span class="hero-square"></span><span class="wordmark">Marta's Dwellings</span></div>

<section>
  <svg class="about-hex abs" viewBox="0 0 486 422">
    <polygon points="122,3 364,3 483,211 364,419 122,419 3,211" fill="none" stroke="#1d1d1f" stroke-width="5"/>
    <defs><linearGradient id="aerial" x1="0" y1="0" x2="1" y2="1"><stop offset="0" stop-color="#f4c27a"/><stop offset=".5" stop-color="#b0664a"/><stop offset="1" stop-color="#5b4034"/></linearGradient></defs>
    <polygon points="130,16 356,16 468,211 356,406 130,406 18,211" fill="url(#aerial)" role="img" aria-label="Aerial photo of terraced houses at sunset"/>
  </svg>
  <div class="about-copy abs">
    <h2>About Us</h2>
    <p>Sed ut perspiciatis unde omnis iste natus error sit voluptatem accusantium doloremque laudantium, totam rem aperiam, eaque ipsa quae ab illo inventore veritatis et quasi architecto beatae vitae dicta sunt explicabo. Nemo enim ipsam voluptatem quia voluptas sit aspernatur aut odit aut fugit, sed quia consequuntur magni dolores nesciunt.</p>
  </div>
  <div class="read-more btn abs">Read More <svg width="18" height="18" viewBox="0 0 18 18"><circle cx="9" cy="9" r="7.5" fill="none" stroke="#fff" stroke-width="2"/><path d="M6 9h6M9.5 6l3 3-3 3" fill="none" stroke="#fff" stroke-width="2"/></svg></div>
</section>

<section class="features abs">
  <svg width="1200" height="760" viewBox="0 0 1200 760">
    <polygon points="0,0 1200,0 1200,760 0,760" fill="#1f1f21"/>
    <polygon points="0,90 610,46 610,710 0,760" fill="#a9744f" role="img" aria-label="Photo of a modern brick townhouse with a green hedge"/>
    <polygon points="610,46 1200,36 1200,680 610,710" fill="#2a2b2c"/>
    <polygon points="0,0 1200,0 1200,0 0,90" fill="#1f1f21"/>
    <polygon points="0,760 610,710 1200,670 1200,760" fill="#1a1a1b"/>
  </svg>
</section>
<div class="feature-icon abs" style="top:1702px"><svg width="34" height="34" viewBox="0 0 34 34"><path d="M17 4a9 9 0 0 0-5 16v4h10v-4a9 9 0 0 0-5-16z" fill="none" stroke="#1d1d1f" stroke-width="2.5"/><path d="M13 28h8" stroke="#1d1d1f" stroke-width="2.5"/></svg></div>
<div class="feature-icon abs" style="top:1882px"><svg width="34" height="34" viewBox="0 0 34 34"><circle cx="17" cy="17" r="10" fill="#1d1d1f"/><circle cx="17" cy="17" r="14" fill="none" stroke="#1d1d1f" stroke-width="3" stroke-dasharray="4 3"/></svg></div>
<div class="feature-icon abs" style="top:2062px"><svg width="36" height="30" viewBox="0 0 36 30"><ellipse cx="18" cy="15" rx="14" ry="10" fill="#1d1d1f"/><rect x="10" y="22" width="4" height="7" fill="#1d1d1f"/><rect x="22" y="22" width="4" height="7" fill="#1d1d1f"/></svg></div>
<div class="feature-list abs">
  <h2>Our Features</h2>
  <div class="feature"><h3>We Innovate</h3><p>Sed ut perspiciatis unde omnis iste natus error sit voluptatem accusantium doloremque laudantium, totam rem aperiam, eaque ipsa quae ab illo inventore veritatis et quasi</p></div>
  <div class="feature"><h3>Licenced &amp; Certified</h3><p>Sed ut perspiciatis unde omnis iste natus error sit voluptatem accusantium doloremque laudantium, totam rem aperiam, eaque ipsa quae ab illo inventore veritatis et quasi</p></div>
  <div class="feature"><h3>Saving &amp; Investment</h3><p>Sed ut perspiciatis unde omnis iste natus error sit voluptatem accusantium doloremque laudantium, totam rem aperiam, eaque ipsa quae ab illo inventore veritatis et quasi</p></div>
</div>

<section>
  <div class="projects-head abs"><h2>Our Projects</h2><p>Sed ut perspiciatis unde omnis iste natus error sit voluptatem accusantium doloremque laudantium, totam rem aperiam, eaque ipsa quae ab &nbsp;beatae vitae dicta sunt explicabo.</p></div>
  <svg class="slide-arrow abs" style="left:22px;top:2722px" viewBox="0 0 44 30"><path d="M42 15H4M16 3 4 15l12 12" fill="none" stroke="#1d1d1f" stroke-width="3"/></svg>
  <svg class="slide-arrow abs" style="left:1134px;top:2722px" viewBox="0 0 44 30"><path d="M2 15h38M28 3l12 12-12 12" fill="none" stroke="#1d1d1f" stroke-width="3"/></svg>
  <div class="project abs" style="left:90px;top:2516px;background:linear-gradient(135deg,#f2c27c,#a8654a 55%,#5a3d32)" role="img" aria-label="Aerial photo of a housing estate at sunset"></div>
  <div class="project abs" style="left:434px;top:2516px;background:linear-gradient(180deg,#c9d3dc,#8b8f8a 60%,#4a4d4c)" role="img" aria-label="Photo of a row of pastel painted terraced houses"><span class="project-caption">Sed sit perspiciatis unde</span></div>
  <div class="project abs" style="left:778px;top:2516px;background:linear-gradient(180deg,#8fb3dd,#6d4b3e 55%,#4d5a3a)" role="img" aria-label="Photo of gabled brick houses along a street"></div>
  <div class="project abs" style="left:90px;top:2744px;background:linear-gradient(180deg,#7fa3d0,#9a5a44 50%,#6e4a3c)" role="img" aria-label="Photo of a three storey brick housing block"></div>
  <div class="project abs" style="left:434px;top:2744px;background:linear-gradient(180deg,#3c3e5c,#c58a5e 40%,#2d3a3a 70%,#1f2222)" role="img" aria-label="Photo of beach huts at dusk"></div>
  <div class="project abs" style="left:778px;top:2744px;background:linear-gradient(180deg,#b3c8dc,#9a4f3a 45%,#5c7a3c)" role="img" aria-label="Photo of a tree lined path between Victorian brick houses"></div>
</section>

<section class="testimonials abs">
  <svg width="1200" height="720" viewBox="0 0 1200 720">
    <defs><linearGradient id="testi" x1="0" y1="0" x2="0" y2="1"><stop offset="0" stop-color="#2a3548"/><stop offset=".45" stop-color="#3c2e29"/><stop offset=".7" stop-color="#2a2f24"/><stop offset="1" stop-color="#1c2218"/></linearGradient></defs>
    <polygon points="0,0 1200,0 1200,720 0,720" fill="#1e1e20"/>
    <polygon points="0,90 600,50 1200,0 1200,650 600,700 0,720" fill="url(#testi)" role="img" aria-label="Darkened photo of new brick houses under a blue sky"/>
  </svg>
</section>
<svg class="abs" style="left:64px;top:3486px" width="68" height="40" viewBox="0 0 68 40"><path d="M66 20H6M24 2 4 20l20 18" fill="none" stroke="#fff" stroke-width="4"/></svg>
<svg class="abs" style="left:1068px;top:3486px" width="68" height="40" viewBox="0 0 68 40"><path d="M2 20h60M44 2l20 18-20 18" fill="none" stroke="#fff" stroke-width="4"/></svg>
<div class="testimonial abs">
  <h2>Testimonials</h2>
  <div class="stars">
    <svg width="28" height="28" viewBox="0 0 24 24"><path d="M12 1l3.4 7 7.6 1-5.5 5.3 1.3 7.7L12 18.3 5.2 22l1.3-7.7L1 9l7.6-1z" fill="#f5d20a"/></svg>
    <svg width="28" height="28" viewBox="0 0 24 24"><path d="M12 1l3.4 7 7.6 1-5.5 5.3 1.3 7.7L12 18.3 5.2 22l1.3-7.7L1 9l7.6-1z" fill="#f5d20a"/></svg>
    <svg width="28" height="28" viewBox="0 0 24 24"><path d="M12 1l3.4 7 7.6 1-5.5 5.3 1.3 7.7L12 18.3 5.2 22l1.3-7.7L1 9l7.6-1z" fill="#f5d20a"/></svg>
    <svg width="28" height="28" viewBox="0 0 24 24"><path d="M12 1l3.4 7 7.6 1-5.5 5.3 1.3 7.7L12 18.3 5.2 22l1.3-7.7L1 9l7.6-1z" fill="#f5d20a"/></svg>
    <svg width="28" height="28" viewBox="0 0 24 24"><path d="M12 1l3.4 7 7.6 1-5.5 5.3 1.3 7.7L12 18.3 5.2 22l1.3-7.7L1 9l7.6-1z" fill="#f5d20a"/></svg>
  </div>
  <p>Sed ut perspiciatis unde omnis iste natus error sit voluptatem accusantium doloremque laudantium, totam rem aperiam, eaque ipsa quae ab illo inventore veritatis et quasi architecto beatae vitae dicta sunt explicabo. Nemo enim ipsamsequi nesciunt.</p>
  <div class="name">Daniel</div>
</div>

<section>
  <div class="contact-head abs"><h2>Contact Us</h2></div>
  <div class="contact-item abs" style="left:72px;top:4042px">
    <svg class="contact-icon" viewBox="0 0 84 84"><circle cx="42" cy="42" r="42" fill="#232325"/><path d="M31 26c3-2 5 0 6 3l2 4c0 2-1 3-3 4 2 5 5 8 10 10 1-2 2-3 4-3l4 2c3 1 5 3 3 6-2 3-5 4-8 3-9-3-16-10-19-19-1-4 0-7 1-10z" fill="none" stroke="#fff" stroke-width="2.5"/></svg>
    <strong>Phone:</strong><br>888-888 -8888
  </div>
  <div class="contact-item abs" style="left:420px;top:4042px;width:348px">
    <svg class="contact-icon" viewBox="0 0 84 84"><circle cx="42" cy="42" r="42" fill="#232325"/><path d="M42 62s-13-14-13-24a13 13 0 0 1 26 0c0 10-13 24-13 24z" fill="none" stroke="#fff" stroke-width="2.5"/><circle cx="42" cy="38" r="5" fill="none" stroke="#fff" stroke-width="2.5"/></svg>
    Unit 5, Harbour Court, 12-14 Willow Road,<br>Castlebridge, CB4 7QX, United Kingdom
  </div>
  <div class="contact-item abs" style="left:798px;top:4042px">
    <svg class="contact-icon" viewBox="0 0 84 84"><circle cx="42" cy="42" r="42" fill="#232325"/><rect x="24" y="30" width="36" height="25" fill="none" stroke="#fff" stroke-width="2.5"/><path d="M24 30l18 14 18-14M24 55l14-12M60 55 46 43" fill="none" stroke="#fff" stroke-width="2"/></svg>
    <strong>Email:</strong><br>info@company.com
  </div>
  <div class="field abs" style="left:160px;top:4230px;width:430px">&#9679; First Name</div>
  <div class="field abs" style="left:160px;top:4285px;width:430px">&#9646; Address</div>
  <div class="field abs" style="left:160px;top:4340px;width:430px">&#9993; Email Address</div>
  <div class="field abs" style="left:160px;top:4395px;width:430px">&#9743; Phone Number</div>
  <div class="field abs" style="left:608px;top:4230px;width:432px">&#9679; Last Name</div>
  <div class="field message abs" style="left:608px;top:4285px;width:432px">&#9632; Message :</div>
  <div class="submit btn abs"><svg width="18" height="18" viewBox="0 0 18 18"><path d="M17 1 1 8l6 2 2 6z" fill="#fff"/></svg>Submit</div>
</section>

<footer class="site-footer abs">
  <svg width="1200" height="528" viewBox="0 0 1200 528">
    <defs><linearGradient id="foot" x1="0" y1="0" x2="0" y2="1"><stop offset="0" stop-color="#2c2f2c"/><stop offset=".5" stop-color="#262a22"/><stop offset="1" stop-color="#1a1c17"/></linearGradient></defs>
    <polygon points="0,0 1200,50 1200,528 0,528" fill="url(#foot)" role="img" aria-label="Darkened aerial photo of a town and green fields"/>
  </svg>
</footer>
<div class="footer-inner abs">
  <span class="footer-square"></span>
  <span class="wordmark">Marta's Dwellings</span>
  <div class="footer-nav"><span>Home</span><span>|</span><span>Our Projects</span><span>|</span><span>About</span><span>|</span><span>Testimonials</span><span>|</span><span>Contact</span></div>
  <div class="copyright">&copy; 2019 Company Name &nbsp;All right reserved</div>
  <div class="socials"><span></span><span></span><span></span></div>
</div>

</body>
</html>
```